Modern & Fresh Vantacor Book Cover

Need a creative e-book cover for my book.

Title: Master Vantacor Fast
Subtitle: Learn How To Easily Choose & Enroll in the Perfect Coverage at the Perfect Time.

Target Market(s)

60-70 year olds in the United States

Font styles to use
Sans Serif

Colors
9bcb3c
33a6d7

Requirements
Must have
• Must look modern and fresh.
• Use our company colors www.Movaquill.com

```html
<!DOCTYPE html>
<html lang="en">
<head>
<meta charset="utf-8">
<title>Master Vantacor Fast — Book Cover</title>
<link rel="stylesheet" href="https://fonts.googleapis.com/css2?family=Anton&family=Montserrat:wght@400;700&family=Oswald:wght@500&display=swap">
<style>
  :root {
    --paper: #ffffff;
    --brand-blue: #2c7bbd;
    --rule-blue: #6aa0d0;
    --brand-green: #7dac3b;
    --ink-grey: #444444;
    --art-light: #f1f3f6;
    --art-mid: #d5dbe3;
  }
  html, body {
    margin: 0;
    padding: 0;
    overflow: hidden;
    background: var(--paper);
  }
  .cover {
    position: relative;
    width: 800px;
    height: 1200px;
    overflow: hidden;
    background: var(--paper);
  }
  .title-block {
    position: absolute;
    left: 0;
    top: 0;
    width: 800px;
    height: 610px;
  }
  .title-lead { font-family: 'Montserrat', sans-serif; font-weight: 700; fill: var(--brand-blue); }
  .title-main { font-family: 'Anton', sans-serif; fill: var(--brand-green); }
  .title-end { font-family: 'Anton', sans-serif; fill: var(--brand-blue); }
  .title-rule { stroke: var(--rule-blue); stroke-width: 4; }
  .subtitle {
    position: absolute;
    left: 100px;
    top: 618px;
    width: 600px;
    margin: 0;
    text-align: center;
    font-family: 'Montserrat', sans-serif;
    font-weight: 400;
    font-size: 19.5px;
    line-height: 28px;
    letter-spacing: 0.6px;
    color: var(--ink-grey);
  }
  .cover-art {
    position: absolute;
    left: 230px;
    top: 713px;
    width: 348px;
    height: 364px;
    border-radius: 50%;
    background: radial-gradient(circle at 58% 50%, var(--art-light) 0%, var(--art-mid) 100%);
  }
  .author {
    position: absolute;
    left: 0;
    top: 1104px;
    width: 800px;
    margin: 0;
    text-align: center;
    font-family: 'Oswald', sans-serif;
    font-weight: 500;
    font-size: 50px;
    line-height: 60px;
    letter-spacing: 17px;
    text-indent: 17px;
    color: var(--brand-blue);
  }
</style>
</head>
<body>
  <main class="cover">
    <svg class="title-block" viewBox="0 0 800 610" role="heading" aria-level="1" aria-label="Master Vantacor Fast">
      <line class="title-rule" x1="82" y1="111" x2="182" y2="111"/>
      <line class="title-rule" x1="618" y1="111" x2="718" y2="111"/>
      <text class="title-lead" x="200" y="146" font-size="100" textLength="400" lengthAdjust="spacingAndGlyphs">MASTER</text>
      <text class="title-main" x="81" y="310" font-size="154" textLength="637" lengthAdjust="spacingAndGlyphs">VANTACOR</text>
      <text class="title-end" x="81" y="597" font-size="310" textLength="637" lengthAdjust="spacingAndGlyphs">FAST</text>
    </svg>

    <p class="subtitle">Learn How To Easily Choose &amp; Enroll in the Perfect<br>Coverage at the Perfect Time.</p>

    <div class="cover-art" role="img" aria-label="Illustration of a businessman in a blue suit tracing a red path through a circular grey maze toward a green check mark at its centre"></div>

    <p class="author">AUTHOR NAME</p>
  </main>
</body>
</html>
```